Corvane Capital Business Cards

These are professional business cards that are for my family office.
Put fake emails and phone numbers as of now until I finalize those components. This family office controls my families investments, assets, and future. The cards should be professional.
..
.
.
.
I just uploaded another variation of a logo I would like to see as a business card to I am inbeteen which logo to use

Target Market(s)

business

Industry/Entity Type

business

Contact Information for Business Card

Professional, wealth related, finance related.

Requirements
Must have
• Logo

```html
<!DOCTYPE html>
<html lang="en">
<head>
<meta charset="utf-8">
<title>Corvane Capital Business Cards</title>
<link href="https://fonts.googleapis.com/css2?family=Cinzel:wght@500&family=Montserrat:wght@400;500;700&display=swap" rel="stylesheet">
<style>
  :root {
    --navy: #1b2030;
    --navy-deep: #151a28;
    --navy-emboss: #232a3d;
    --grey: #a9a9a9;
    --paper: #ffffff;
    --ink: #1c1f2a;
    --stage: #2a2a2c;
  }
  * { margin: 0; padding: 0; box-sizing: border-box; }
  html, body {
    width: 1200px; height: 874px; overflow: hidden;
    background: var(--stage);
  }
  .stage {
    position: relative; width: 1200px; height: 874px;
  }
  .card {
    position: absolute; left: 250px; width: 700px; height: 400px;
    border-radius: 26px; overflow: hidden;
  }
  /* back */
  .card-back { top: 24px; background: var(--navy); }
  .back-wordmark {
    position: absolute; left: 0; right: 0; top: 168px;
    text-align: center;
    font-family: "Cinzel", serif; font-weight: 500; font-size: 54px;
    letter-spacing: 2px; color: var(--navy-emboss);
  }
  /* front */
  .card-front { top: 450px; background: var(--paper); }
  .brand {
    position: absolute; left: 0; width: 320px; top: 62px;
    display: flex; flex-direction: column; align-items: center;
  }
  .brand-circle {
    width: 104px; height: 104px; border-radius: 50%;
    border: 4px solid var(--navy);
  }
  .brand-name {
    margin-top: 16px;
    font-family: "Cinzel", serif; font-weight: 500; font-size: 26px;
    color: var(--navy); letter-spacing: 1px;
  }
  .divider {
    position: absolute; left: 334px; top: 52px; width: 2px; height: 218px;
    background: var(--navy);
  }
  .contact {
    position: absolute; left: 366px; top: 56px;
    font-family: "Montserrat", sans-serif; color: var(--ink);
  }
  .person-name { font-weight: 700; font-size: 25px; line-height: 1.1; }
  .person-title { font-size: 13px; margin-top: 2px; }
  .address { font-size: 14px; line-height: 1.35; margin-top: 18px; }
  .lines { list-style: none; margin-top: 10px; }
  .lines li {
    display: flex; align-items: center; gap: 10px;
    font-size: 14px; line-height: 1.75;
  }
  .lines svg { width: 13px; height: 13px; flex: none; }
  .band-dark {
    position: absolute; left: 0; top: 296px; width: 440px; height: 30px;
    background: var(--navy);
  }
  .band-grey {
    position: absolute; left: 440px; right: 0; top: 344px; height: 30px;
    background: var(--grey);
  }
  .band-seal {
    position: absolute; left: 412px; top: 318px; width: 58px; height: 58px;
    border-radius: 50%; background: var(--paper);
    border: 3px solid var(--navy);
  }
</style>
</head>
<body>
<main class="stage">
  <section class="card card-back" aria-label="Card back">
    <div class="back-wordmark">Corvane Capital</div>
  </section>

  <section class="card card-front" aria-label="Card front">
    <div class="brand">
      <div class="brand-circle"></div>
      <div class="brand-name">Corvane Capital</div>
    </div>
    <div class="divider"></div>
    <div class="contact">
      <div class="person-name">Marcus Ellery</div>
      <div class="person-title">Owner</div>
      <div class="address">48 Harbor Crest Lane<br>Fairhaven, NJ 07704 USA</div>
      <ul class="lines">
        <li>
          <svg viewBox="0 0 16 16" aria-hidden="true"><path fill="#1c1f2a" d="M3.6 1.2l2.3 2.6-1.3 1.7c.9 2 2.4 3.5 4.4 4.4l1.7-1.3 2.6 2.3-1.2 2.3C6.8 13.5 2.5 9.2 1.3 3.9z"/></svg>
          (555)204-7186
        </li>
        <li>
          <svg viewBox="0 0 16 16" aria-hidden="true"><rect x="1" y="3" width="14" height="10" rx="1" fill="#1c1f2a"/><path d="M1.5 3.8L8 9l6.5-5.2" stroke="#fff" stroke-width="1.2" fill="none"/></svg>
          info@yourwebsitename.com
        </li>
        <li>
          <svg viewBox="0 0 16 16" aria-hidden="true"><circle cx="8" cy="8" r="7" fill="#1c1f2a"/><path d="M1 8h14M8 1c-3 3-3 11 0 14M8 1c3 3 3 11 0 14" stroke="#fff" stroke-width="1" fill="none"/></svg>
          www.yourwebsitename.com
        </li>
      </ul>
    </div>
    <div class="band-dark"></div>
    <div class="band-grey"></div>
    <div class="band-seal"></div>
  </section>
</main>
</body>
</html>
```